Business Cards Needed for Innovative Healthcare Marketing Company

We are a marketing company focused on healthcare. Our company is all about rebranding yourself renewing your image and generating results. The phoenix stands for "reborn" or "rising" which we provide new brands for our clients we take their old brands and renew it with creativity and innovation. I am looking for a business card with color dimension. I have attached an example of a card I think has the look and feel of what I am trying to accomplish. I like that the card example has black and grey font colors, I like the font placement and the small logo, I really like the use of the colors on the right those are the colors of my logo. My logo is phoenix so maybe incorporating flames similar to that design. I would like the back a solid color maybe red with an opaque version of the logo and website. As a marketing company I am always open to creative liberty!

Target Market(s)

Doctors and business professionals.

Industry/Entity Type

Marketing

Contact Information for Business Card

Valcorne Health Care Marketing
Marla Tenwick- CEO
#(512)638-2974
email-marla@valcorne.com
website- valcorne.com

Font styles to use
Sans Serif

Colors
ec1f27
f37122
ffc214
fbed22
fbf289
f04a50

Requirements
Must have
• The logo and required information
Nice to have
• icons by the information
Should not have
• child like font

```html
<!DOCTYPE html>
<html lang="en">
<head>
<meta charset="utf-8">
<title>Valcorne Health Care Marketing – Business Card</title>
<link rel="stylesheet" href="https://fonts.googleapis.com/css2?family=Open+Sans:wght@300;400;600;700&display=swap">
<style>
  :root {
    --stage: #3b3b3b;
    --frame-red: #c8232a;
    --brand-red: #ec1f27;
    --brand-orange: #f37122;
    --brand-amber: #ffc214;
    --face-white: #ffffff;
    --face-black: #0c0c0c;
    --text-light: #f2f2f2;
    --text-grey: #9a9a9a;
  }
  * { box-sizing: border-box; margin: 0; padding: 0; }
  html, body {
    width: 1200px; height: 950px; overflow: hidden;
    background: var(--stage);
    font-family: "Open Sans", Arial, sans-serif;
  }
  .stage { position: relative; width: 1200px; height: 950px; }

  .card {
    position: absolute;
    width: 640px; height: 366px;
    border-radius: 22px;
    background: var(--frame-red);
    padding: 16px;
    box-shadow: 0 18px 40px rgba(0,0,0,.45);
  }
  .card-face {
    width: 100%; height: 100%;
    border-radius: 14px;
    position: relative;
    overflow: hidden;
  }

  /* Front */
  .card-front { left: 150px; top: 60px; }
  .card-front .card-face {
    background: var(--face-white);
    display: flex; align-items: center; justify-content: center;
  }
  .brand-lockup { display: flex; align-items: center; gap: 20px; }
  .brand-dot {
    width: 58px; height: 58px; border-radius: 50%;
    background: linear-gradient(135deg, var(--brand-amber), var(--brand-orange) 50%, var(--brand-red));
  }
  .brand-name {
    color: var(--brand-red);
    font-weight: 300;
    font-size: 40px;
    letter-spacing: 2px;
    line-height: 1.05;
    text-transform: uppercase;
  }
  .brand-name small {
    display: block;
    font-size: 14px;
    letter-spacing: 3px;
    margin-top: 6px;
  }

  /* Back */
  .card-back { left: 410px; top: 510px; }
  .card-back .card-face {
    background: linear-gradient(120deg, #1c1c1c 0%, var(--face-black) 55%, #1a1a1a 100%);
    display: flex; align-items: center;
    padding: 0 40px 0 48px;
  }
  .contact-list { list-style: none; flex: 1; }
  .contact-item {
    display: flex; align-items: center; gap: 14px;
    color: var(--text-light);
    font-size: 17px;
    margin-bottom: 12px;
  }
  .contact-item.no-icon { padding-left: 42px; margin-top: -6px; }
  .contact-name {
    color: var(--brand-red);
    font-weight: 600;
    font-size: 24px;
  }
  .contact-title { font-weight: 700; font-size: 16px; }
  .icon {
    width: 28px; height: 28px; flex: none;
    background: var(--brand-red);
    border-radius: 3px;
    display: flex; align-items: center; justify-content: center;
  }
  .icon svg { width: 18px; height: 18px; }

  .back-mark {
    display: flex; flex-direction: column; align-items: center; gap: 14px;
    width: 210px;
  }
  .back-mark .brand-dot { width: 120px; height: 120px; }
  .back-mark .brand-name {
    color: var(--brand-orange);
    font-size: 24px;
  }
</style>
</head>
<body>
<main class="stage">

  <section class="card card-front" aria-label="Card front">
    <div class="card-face">
      <div class="brand-lockup">
        <span class="brand-dot" aria-hidden="true"></span>
        <p class="brand-name">Valcorne<small>Health Care Marketing</small></p>
      </div>
    </div>
  </section>

  <section class="card card-back" aria-label="Card back">
    <div class="card-face">
      <ul class="contact-list">
        <li class="contact-item">
          <span class="icon"><svg viewBox="0 0 24 24" fill="#fff"><circle cx="12" cy="8" r="4.5"/><path d="M3 22c0-5 4-8 9-8s9 3 9 8z"/></svg></span>
          <span class="contact-name">Marla Tenwick</span>
        </li>
        <li class="contact-item no-icon"><span class="contact-title">CEO</span></li>
        <li class="contact-item">
          <span class="icon"><svg viewBox="0 0 24 24" fill="#fff"><path d="M6.6 10.8a15.5 15.5 0 0 0 6.6 6.6l2.2-2.2a1 1 0 0 1 1-.25 11.4 11.4 0 0 0 3.6.57 1 1 0 0 1 1 1V20a1 1 0 0 1-1 1A17 17 0 0 1 3 4a1 1 0 0 1 1-1h3.5a1 1 0 0 1 1 1c0 1.25.2 2.45.57 3.57a1 1 0 0 1-.25 1z"/></svg></span>
          <span>(512)638-2974</span>
        </li>
        <li class="contact-item">
          <span class="icon"><svg viewBox="0 0 24 24" fill="none" stroke="#fff" stroke-width="2"><rect x="3" y="6" width="18" height="13" rx="1.5"/><path d="M3 7l9 7 9-7"/></svg></span>
          <span>marla@valcorne.com</span>
        </li>
        <li class="contact-item">
          <span class="icon"><svg viewBox="0 0 24 24" fill="none" stroke="#fff" stroke-width="1.8"><circle cx="12" cy="12" r="9"/><path d="M3 12h18M12 3c3 3.5 3 14.5 0 18M12 3c-3 3.5-3 14.5 0 18"/></svg></span>
          <span>www.valcorne.com</span>
        </li>
      </ul>
      <div class="back-mark">
        <span class="brand-dot" aria-hidden="true"></span>
        <p class="brand-name">Valcorne</p>
      </div>
    </div>
  </section>

</main>
</body>
</html>
```